Tovel & Associates - London New Letting and Property Management Company *

Tovel & Associates LTD is a new company based in London, and works with brand new residential property in the city centre.

We are aiming to have 1000 new properties a year.

We are looking for something modern and minimalistic :
Logo ,Monogram, Paper Head and Business Card.

Target Market(s)

Internation landlords

Industry/Entity Type

Real Estate

Logo Text

Tovel & Associates

Colors

Designer to choose colors to be used in the design.

Requirements
Nice to have
• A particular monogram with "TA"
Should not have
• Little House over the logo

```html
<!DOCTYPE html>
<html lang="en">
<head>
<meta charset="utf-8">
<title>Tovel &amp; Associates – Stationery</title>
<link rel="stylesheet" href="https://fonts.googleapis.com/css2?family=Open+Sans:wght@400;600;700&family=Lato:wght@400;700&display=swap">
<style>
:root{
  --bg:#dadada;
  --paper:#f2f2f2;
  --navy:#1b4f72;
  --sky:#27a8e0;
  --text:#6b6b6b;
  --dark:#4a4a4a;
  --rule:#4f6f8f;
}
*{margin:0;padding:0;box-sizing:border-box}
html,body{width:1200px;height:1062px;overflow:hidden;background:var(--bg)}
body{position:relative;font-family:"Open Sans",sans-serif}

.letterhead{position:absolute;left:115px;top:94px;width:585px;height:876px;background:var(--paper);box-shadow:0 2px 6px rgba(0,0,0,.12)}
.wordmark{display:flex;align-items:center;gap:10px;font-family:"Open Sans",sans-serif;font-weight:700;color:var(--navy);text-transform:uppercase;white-space:nowrap}
.wordmark .mark{display:block;background:var(--navy)}
.letterhead .wordmark{position:absolute;left:0;right:0;top:82px;justify-content:center;font-size:21px;letter-spacing:1px}
.letterhead .wordmark .mark{width:22px;height:22px}

.salutation{position:absolute;left:40px;top:188px;font-size:17px;color:var(--dark)}
.letter-body{position:absolute;left:40px;top:242px;width:508px}
.letter-body p{font-size:11.4px;line-height:16.4px;color:var(--text);margin-bottom:19px}
.signoff{position:absolute;left:40px;top:628px;font-family:"Lato",sans-serif;color:var(--dark)}
.signoff .regards{font-size:15px}
.signature{display:block;width:112px;height:22px;margin:8px 0 8px;background:linear-gradient(90deg,#bdbdbd,#d8d8d8);border-radius:11px}
.signoff .name{font-size:14px}
.signoff .role{font-size:11px;font-weight:700;color:#555;margin-top:2px}
.signoff .company{font-size:8px;font-weight:700;color:#555;text-transform:uppercase;margin-top:6px}
.letter-foot{position:absolute;left:40px;right:40px;top:794px;border-top:1.5px solid var(--rule);padding-top:16px;text-align:center;font-size:12px;line-height:20px;color:var(--text);letter-spacing:.2px;white-space:nowrap}
.letter-foot b{color:var(--navy);font-weight:600}

.logo-large{position:absolute;left:768px;top:250px}
.logo-large.wordmark{font-size:27px;letter-spacing:1px;gap:14px}
.logo-large .mark{width:34px;height:34px}

.card{position:absolute;left:716px;width:374px;height:213px;box-shadow:0 2px 6px rgba(0,0,0,.12)}
.card-front{top:475px;background:var(--paper)}
.card-front .wordmark{position:absolute;right:17px;top:32px;font-size:13px;gap:7px}
.card-front .wordmark .mark{width:14px;height:14px}
.card-name{position:absolute;left:16px;top:120px;font-size:15px;font-weight:600;color:var(--navy);letter-spacing:.5px}
.card-role{position:absolute;left:16px;top:140px;font-size:9.5px;color:var(--text)}
.card-contact{position:absolute;left:16px;right:17px;top:162px;border-top:1px solid var(--rule);padding-top:10px;font-family:"Lato",sans-serif;font-size:8.6px;line-height:14px;color:var(--dark);white-space:nowrap}
.card-contact b{color:var(--navy);font-weight:700}
.card-back{top:726px;background:var(--navy)}
.card-back .wordmark{position:absolute;left:0;right:0;top:92px;justify-content:center;color:#fff;font-size:18px;letter-spacing:1px}
.card-back .wordmark .mark{width:20px;height:20px;background:var(--sky)}
</style>
</head>
<body>

<section class="letterhead">
  <div class="wordmark"><span class="mark"></span>Tovel &amp; Associates</div>
  <p class="salutation">Dear Sir</p>
  <div class="letter-body">
    <p>Lorem ipsum dolor sit amet, an vel recteque dissentiet, detracto albucius platonem ex vel, eros repudiandae cu. Atqui aliquando nec an, unum graece adolescens vel ad. Id odio scae has, iudico euismod atomorum ius ea, cum ea honestatis quaerendum theophrastus. Mea honestatis quaerendum theophrastus. Mea</p>
    <p>Lorem ipsum dolor sit amet, an vel recteque dissentiet, detracto albucius platonem ex vel, eros repudiandae cu. Atqui aliquando nec an, unum graece adolescens vel ad. Id odio scae has, iudico euismod atomorum ius ea, cum ea honestatis quaerendum theophrastus. Mea doming repudiandae ex, cu cum civibus assentior posidonium. Quo etiam pertinax ex, te eros repudiandae cu. Atqui aliquando nec an, unum graece adolescens vel ad. Id odio scae honestatis quaerendum theophrastus. Mea</p>
    <p>Lorem ipsum dolor sit amet, an vel recteque dissentiet, detracto albucius platonem ex vel, eros repudiandae cu. Atqui aliquando nec an, unum graece adolescens vel ad. Id odio scae has, iudico euismod atomorum ius ea, cum ea honestatis quaerendum theophrastus. Mea honestatis quaerendum theophrastus. Mea</p>
    <p>Lorem ipsum dolor sit amet, an vel recteque dissentiet, detracto albucius platonem ex vel, eros repudiandae cu. Atqui aliquando nec an, unum graece adolescens vel ad. Id odio scae has, iudico euismod atomorum ius ea, cum ea honestatis quaerendum theophrastus. Mea honestatis quaerendum theophrastus. Mea</p>
  </div>
  <div class="signoff">
    <p class="regards">Kind Regards</p>
    <span class="signature" role="img" aria-label="Handwritten signature of Oliver Hastings"></span>
    <p class="name">Oliver Hastings</p>
    <p class="role">Chief Alchemist</p>
    <p class="company">Halden Corporate Services Ltd</p>
  </div>
  <div class="letter-foot">
    <b>P</b> : +44 20 7946 0321 | <b>E</b> : info@tovelassoc.com | <b>W</b> : www.<b>tovelassoc</b>.com<br>
    <b>A</b> : 14 Harrow Lane London W2 4RT
  </div>
</section>

<div class="logo-large wordmark"><span class="mark"></span>Tovel &amp; Associates</div>

<section class="card card-front">
  <div class="wordmark"><span class="mark"></span>Tovel &amp; Associates</div>
  <p class="card-name">DANIEL WREN</p>
  <p class="card-role">Director</p>
  <div class="card-contact">
    <b>P</b> : +44 20 7946 0321 | <b>E</b> : info@tovelassoc.com | <b>W</b> : www.<b>tovelassoc</b>.com<br>
    <b>A</b> : 14 Harrow Lane London W2 4RT
  </div>
</section>

<section class="card card-back">
  <div class="wordmark"><span class="mark"></span>Tovel &amp; Associates</div>
</section>

</body>
</html>
```